Help design website for "Brightwater Civic Advisors" to advance the common good

Here is the Google doc link that lays out the design:

https://files.plumrivet.example/sheet/d/7QmTzR2wLx9KpVbN4hJcY8sEaUoFdG3iXkMnPq5rWt6/edit?usp=sharing

Here is the Google drive folder with the logos and photos: https://vault.plumrivet.example/open?id=4HkWp9LzQe2TxRvN8mBaYc3DsUoJfG6

The testimonials are being gathered and will be shared by Friday, 1/4.

The winner will also have to migrate the coding files to my hosting site.

Thank you for your help! Looking forward to seeing your designs.

Target Market(s)

Prospective clients

Industry/Entity Type

Non Profit

Coding

Coded - Design and coding required

Number of Pages Required

5+ page

Requirements
Must have
• Noted in the Google doc regarding layout.
Nice to have

```html
<!DOCTYPE html>
<html lang="en">
<head>
<meta charset="utf-8">
<title>About — Brightwater Civic Advisors</title>
<link href="https://fonts.googleapis.com/css2?family=Poppins:wght@500;600;700&family=Open+Sans:wght@400;600&display=swap" rel="stylesheet">
<style>
:root{
  --brand-blue:#3d8bd0;
  --page-bg:#f3f1f1;
  --white:#ffffff;
  --ink:#2b2b2b;
  --body-ink:#333333;
  --footer-bg:#262830;
  --pattern-a:#f1f1f1;
  --pattern-b:#e4e4e4;
  --photo-a:#5a4a40;
  --photo-b:#9aa2a8;
  --partner-maroon:#7a1616;
  --partner-blue:#1f8fd1;
  --partner-green:#59b52f;
  --partner-navy:#2f4f9a;
  --partner-black:#1a1a1a;
}
*{box-sizing:border-box;margin:0;padding:0}
html,body{width:836px;height:1200px;overflow:hidden;background:var(--white)}
body{position:relative;font-family:"Open Sans",Arial,sans-serif;color:var(--body-ink)}
.abs{position:absolute}

/* header */
.site-header{left:0;top:0;width:836px;height:106px;background:var(--brand-blue)}
.brand{left:100px;top:14px;display:flex;align-items:center;gap:10px}
.brand-square{width:14px;height:14px;background:var(--white)}
.brand-name{font-family:"Poppins",sans-serif;font-weight:500;color:var(--white);font-size:19px;letter-spacing:4px;line-height:22px;text-transform:uppercase}
.cta-button{left:513px;top:18px;width:222px;height:36px;border:2px solid var(--white);color:var(--white);font-family:"Poppins",sans-serif;font-weight:700;font-size:9.6px;display:flex;align-items:center;justify-content:center;text-transform:uppercase}
.main-nav{left:410px;top:76px;display:flex;gap:14px;font-family:"Poppins",sans-serif;font-weight:700;font-size:9.6px;color:var(--white);text-transform:uppercase}

/* about */
.about-band{left:0;top:106px;width:836px;height:560px;background:var(--page-bg)}
.portrait{left:98px;top:159px;width:246px;height:246px;border-radius:50%;background:radial-gradient(circle at 50% 45%,var(--photo-a) 0%,#3b3431 45%,var(--photo-b) 100%);box-shadow:0 6px 14px rgba(0,0,0,.25)}
.about-title{left:387px;top:140px;font-family:"Poppins",sans-serif;font-weight:700;font-size:16.5px;color:var(--ink)}
.about-copy{left:386px;top:182px;width:356px;font-size:10.3px;line-height:14px}
.about-copy p{margin-bottom:14px}
.about-copy p.spaced{margin-top:20px}
.resume-button{left:390px;top:504px;width:128px;height:31px;background:var(--brand-blue);color:var(--white);font-family:"Poppins",sans-serif;font-weight:700;font-size:11.5px;display:flex;align-items:center;justify-content:center;text-transform:uppercase}

.divider-svg{left:0;top:590px}

/* work history */
.history-title{left:0;top:640px;width:836px;text-align:center;font-family:"Poppins",sans-serif;font-weight:700;font-size:17px;color:var(--ink)}
.partner{display:flex;align-items:center;gap:8px;font-family:"Poppins",sans-serif;font-weight:700;font-size:14px}
.partner-mark{width:14px;height:14px}
.partner--campus{left:98px;top:732px;color:var(--partner-maroon)}
.partner--campus .partner-mark{background:var(--partner-maroon)}
.partner--fellows{left:352px;top:684px;width:108px;height:110px;background:#f7f7f7;color:var(--partner-black);flex-direction:column;justify-content:center;font-size:12px;text-align:center}
.partner--fellows .partner-mark{border-radius:50%;width:36px;height:36px;background:var(--partner-blue)}
.partner--summit{left:530px;top:732px;color:var(--partner-green);font-size:16px}
.partner--neighbors{left:98px;top:840px;color:var(--partner-navy)}
.partner--neighbors .partner-mark{background:#e0a21a}
.partner--corps{left:375px;top:808px;flex-direction:column;color:var(--partner-black);font-size:11px}
.partner--corps .partner-mark{width:84px;height:84px;border-radius:50%;background:var(--partner-black)}
.partner--exchange{left:526px;top:840px;color:var(--partner-navy);font-size:12px;font-weight:600}
.partner--exchange .partner-mark{background:var(--partner-navy)}

/* footer */
.pattern-band{left:0;top:930px;width:836px;height:130px;background:linear-gradient(180deg,var(--pattern-a),var(--pattern-b))}
.footer-svg{left:0;top:980px}
.footer-brand{left:100px;top:1082px}
.footer-rule{left:427px;top:1070px;width:1px;height:100px;background:#4a4c55}
.footer-menu-title{left:468px;top:1082px;font-family:"Poppins",sans-serif;font-weight:700;font-size:8px;color:var(--white)}
.footer-links{left:468px;top:1107px;font-size:8px;color:var(--white);display:flex;gap:6px}
.footer-copy{left:468px;top:1150px;font-size:7.5px;color:var(--white)}
</style>
</head>
<body>

<header class="abs site-header">
  <div class="abs brand">
    <span class="brand-square"></span>
    <span class="brand-name">Brightwater<br>Civic<br>Advisors</span>
  </div>
  <div class="abs cta-button">Book a complimentary consultation</div>
  <nav class="abs main-nav"><span>About</span><span>Services &amp; Testimonials</span><span>Media &amp; Impact</span><span>Contact</span></nav>
</header>

<section class="abs about-band"></section>
<div class="abs portrait" role="img" aria-label="Portrait photo of founder Dana Holt"></div>
<h1 class="abs about-title">About</h1>
<div class="abs about-copy">
  <p>Brightwater Civic Advisors supports nonprofit organizations and educational institutions to carry out their missions to benefit the wider community.</p>
  <p>Founder Dana Holt is an educator with a 22-year record of demonstrated achievement and leadership roles in nonprofits and educational institutions. Most recently, she served as Associate Dean of Students in the University and Director of the Campus Service Hub at Lakeshore University. Dana has designed, implemented, and evaluated community-based learning and leadership training programs that have attained positive outcomes documented by survey results, recognition by outside agencies, and grants awarded for new initiatives and expansions. She has also significantly and consistently increased the number of program applicants, volunteers, and community partnerships through innovative programming, improved reputation, targeted recruitment, marketing and communications</p>
  <p class="spaced">Dana is a native Chicagoan and has also lived in Tokyo, Boston, San Francisco, and Washington, DC. Dana received her bachelor of arts from Alder College in Fernbrook, MN and her masters in education from Kestrel University in Bayview, MA</p>
</div>
<div class="abs resume-button">Review Resume</div>

<svg class="abs divider-svg" width="836" height="80" viewBox="0 0 836 80" aria-hidden="true">
  <polygon points="0,74 426,4 836,74 836,80 0,80" fill="#ffffff"/>
</svg>

<h2 class="abs history-title">Work History</h2>
<div class="abs partner partner--campus"><span class="partner-mark"></span>Campus Service Hub</div>
<div class="abs partner partner--fellows"><span class="partner-mark"></span>Civic Fellows West</div>
<div class="abs partner partner--summit">Summit Bay Academies</div>
<div class="abs partner partner--neighbors"><span class="partner-mark"></span>Learning Neighbors</div>
<div class="abs partner partner--corps"><span class="partner-mark"></span>Service Corps</div>
<div class="abs partner partner--exchange"><span class="partner-mark"></span>Pacific Teaching Exchange</div>

<div class="abs pattern-band" role="img" aria-label="Faint repeating decorative pattern"></div>
<svg class="abs footer-svg" width="836" height="220" viewBox="0 0 836 220" aria-hidden="true">
  <polygon points="0,77 418,2 836,77 836,220 0,220" fill="#262830"/>
</svg>
<footer>
  <div class="abs brand footer-brand">
    <span class="brand-square"></span>
    <span class="brand-name">Brightwater<br>Civic<br>Advisors</span>
  </div>
  <div class="abs footer-rule"></div>
  <div class="abs footer-menu-title">MENU</div>
  <div class="abs footer-links"><span>ABOUT</span><span>|</span><span>SERVICES &amp; TESTIMONIALS</span><span>|</span><span>MEDIA &amp; IMPACT</span><span>|</span><span>CONTACT</span></div>
  <div class="abs footer-copy">Copyrights @ 2019 All Rights Reserved</div>
</footer>

</body>
</html>
```